Tellmora Corporate Stationery

Look for design of all new corporate stationery for an existing insurance broking business that is going through a redesign and move from older partners to younger family members. New Logo is attached. Company is Brisbane based.
Colours in the Logo is Hex #43bed8 and website features a lot of hex #17b8d8. Website front page "A plan to protect you" - headline. "Professional and Individual advice to protect your greatest assets" - tagline.

Stationery required: Business Cards, Letter head, Thank-you cards, Birthday cards, Presentation folders, With Compliment slips and a powerpoint template. We also would like to send a card to all customers with the something along of the lines of "something new".

Target Market(s)

Customers of Insurance business looking at superannuation, life and income protection insurance, investment advice and wills

Industry/Entity Type

Insurance Broker

Font styles to use
Other font styles liked:
• same as logo

Requirements
Must have
• The above designs for new stationery for the new business including:
• Business Cards, Letter head, Thank-you cards, Birthday cards, Presentation folders, With Compliment slips and a powerpoint template. We also would like to send a card to all customers with the something along of the lines of "something new".
Nice to have
• It is a new look - long time family business being passed to next generation - big focus on advice for YOU, individual advice etc..

```html
<!DOCTYPE html>
<html lang="en">
<head>
<meta charset="utf-8">
<title>Tellmora Business Card</title>
<link rel="stylesheet" href="https://fonts.googleapis.com/css2?family=Open+Sans:ital,wght@0,400;0,600;1,400&display=swap">
<style>
  :root {
    --backdrop: #2b2b2d;
    --paper: #ffffff;
    --brand-cyan: #43bed8;
    --brand-grey: #858689;
    --ink: #3d3d3f;
    --ink-soft: #555558;
  }
  * { margin: 0; padding: 0; box-sizing: border-box; }
  html, body {
    width: 1200px; height: 987px; overflow: hidden;
    background: var(--backdrop);
    font-family: "Open Sans", Arial, sans-serif;
  }
  .card {
    position: absolute; left: 293px; width: 615px; height: 352px;
  }
  .card-front { top: 130px; background: var(--paper); }
  .card-back { top: 505px; background: var(--brand-grey); }

  .name-band {
    position: absolute; left: 0; top: 61px; width: 300px; height: 67px;
    background: var(--brand-cyan); color: #fff; padding: 10px 0 0 26px;
  }
  .person-name { font-size: 22px; font-weight: 600; line-height: 26px; letter-spacing: 0.3px; }
  .person-role { font-size: 16px; font-weight: 400; line-height: 22px; }

  .brand-mark {
    position: absolute; width: 62px; height: 62px; border-radius: 50%;
  }
  .card-front .brand-mark { left: 290px; top: 63px; background: var(--brand-grey); border: 4px solid var(--paper); }
  .brand-name {
    position: absolute; font-weight: 600; letter-spacing: 2px; text-transform: uppercase;
  }
  .card-front .brand-name { left: 376px; top: 70px; font-size: 34px; line-height: 44px; color: var(--brand-cyan); }

  .contact-list { position: absolute; left: 26px; top: 224px; list-style: none; }
  .contact-list li {
    display: flex; align-items: center; height: 23.5px;
    font-size: 16px; color: var(--ink-soft);
  }
  .contact-list svg { width: 15px; height: 15px; margin-right: 8px; fill: var(--brand-cyan); }

  .address {
    position: absolute; right: 21px; top: 248px; text-align: right;
    font-style: normal; font-size: 16px; line-height: 23.5px; color: var(--ink);
  }

  .card-back .brand-mark { left: 368px; top: 220px; width: 40px; height: 40px; background: var(--brand-cyan); }
  .card-back .brand-name { left: 418px; top: 220px; font-size: 27px; line-height: 40px; color: #fff; }
  .back-web {
    position: absolute; right: 31px; top: 312px;
    font-size: 16px; font-style: italic; color: #fff;
  }
</style>
</head>
<body>
  <section class="card card-front">
    <div class="name-band">
      <p class="person-name">MAYA HOLLIS</p>
      <p class="person-role">CEO/FOUNDER</p>
    </div>
    <span class="brand-mark"></span>
    <p class="brand-name">Tellmora</p>

    <ul class="contact-list">
      <li><svg viewBox="0 0 16 16"><path d="M3.5 1l2.6 3-1.5 1.8a9 9 0 0 0 5.6 5.6l1.8-1.5 3 2.6-1.6 2.3C8 15 1 8 1.2 2.6z"/></svg>612 408 5521</li>
      <li><svg viewBox="0 0 16 16"><path d="M4 0h8a1 1 0 0 1 1 1v14a1 1 0 0 1-1 1H4a1 1 0 0 1-1-1V1a1 1 0 0 1 1-1zm1 2v10h6V2zm3 11a1 1 0 1 0 0 2 1 1 0 0 0 0-2z"/></svg>614 372 9018</li>
      <li><svg viewBox="0 0 16 16"><path d="M4 1h8v4H4zM1 6h14v7h-2v-2H3v2H1zm3 6h8v3H4z"/></svg>617 350 2246</li>
      <li><svg viewBox="0 0 16 16"><path d="M1 3h14v10H1zm1.2 1.2L8 8.6l5.8-4.4z" fill-rule="evenodd"/></svg>hello@tellmora.com</li>
    </ul>

    <address class="address">
      42 Wattle Grove Road<br>
      Brisbane, Queensland 4000<br>
      www.tellmora.com
    </address>
  </section>

  <section class="card card-back">
    <span class="brand-mark"></span>
    <p class="brand-name">Tellmora</p>
    <p class="back-web">www.tellmora.com</p>
  </section>
</body>
</html>
```